Animal Horse & Bedding Company Needs a Website Coded & Designed

We need a website for a new animal bedding and feed company that is visually grabbing and vibrant. We would like to see a website that displays trust, quality and confidence. Needs to be responsive and mobile friendly for all browsers and coded for both Android & IOS. SEO is also important.

Joomla or Wordpress – must be both desktop and mobile friendly with fast page load speed. Need the ability to edit ourselves in Wordpress or Joomla.

Full details attached below with some layout and content ideas.

Coding

Coded - Design and coding required

Number of Pages Required

5+ page

Font styles to use
Sans Serif

Requirements
Must have
• Needs to be responsive and mobile friendly for all browsers and coded for both Android & IOS. SEO is also important.

Wordpress – must be both desktop and mobile friendly with fast page load speed. Need the ability to edit ourselves in Wordpress.

Logo Colours:
Dark Brown
CMYK: 50 / 70 / 80 / 70
Pantone: 4625C

Orange
CMYK: 0 / 50 / 100 / 0
Pantone: 144C
Nice to have
• Use picture of building attached and super impose logo on building.

```html
<!DOCTYPE html>
<html lang="en">
<head>
<meta charset="utf-8">
<title>Golden Sheaf – Bedding & Feed</title>
<link href="https://fonts.googleapis.com/css2?family=Oswald:wght@500;600&family=Lato:wght@400;700&display=swap" rel="stylesheet">
<style>
:root{
  --brown:#3d2314;
  --orange:#f7941d;
  --cream:#fdf0e1;
  --grey:#ebebeb;
  --text:#4a4a4a;
  --white:#fff;
  --sky-soft:#dde6ec;
  --field-soft:#b5b9a6;
}
*{box-sizing:border-box;margin:0;padding:0}
html,body{width:1200px;height:3722px;overflow:hidden}
body{position:relative;font-family:'Lato',sans-serif;color:var(--text);background:var(--white)}
.abs{position:absolute}
.head-font{font-family:'Oswald',sans-serif;font-weight:600;color:var(--brown);letter-spacing:1px}
.brand{display:flex;align-items:center;gap:10px}
.brand-dot{width:34px;height:34px;border-radius:50%;background:var(--orange)}
.brand-name{font-family:'Oswald',sans-serif;font-weight:500;color:var(--brown);font-size:28px;letter-spacing:2px;text-transform:uppercase;white-space:nowrap}
.topline{top:0;left:0;width:1200px;height:7px;background:var(--orange)}
.call{left:805px;top:42px;font-size:13px;font-weight:700;color:var(--brown)}
.call .num{color:var(--orange);font-size:15px;display:flex;align-items:center;gap:4px}
.follow{left:1024px;top:40px;font-size:13px;font-weight:700;color:var(--brown)}
.socials{display:flex;gap:3px;margin-top:4px}
.socials span{width:14px;height:14px;border-radius:50%;background:var(--orange)}
.nav{top:113px;left:0;width:1200px;height:32px;background:var(--brown)}
.nav a{position:absolute;top:9px;color:var(--white);font-size:13px;text-decoration:none;text-transform:uppercase}
.nav .sep{position:absolute;top:0;width:1px;height:32px;background:#5a3a27}
.nav .quote{top:0;left:920px;width:173px;height:32px;background:var(--orange);color:var(--brown);font-weight:700;letter-spacing:1.5px;display:flex;align-items:center;justify-content:center}
.hero{top:145px;left:0;width:1200px;height:563px;background:linear-gradient(180deg,var(--sky-soft) 0%,var(--field-soft) 100%)}
.hero h1{position:absolute;top:55px;width:100%;text-align:center;font-size:39px;line-height:41px;color:var(--brown)}
.btn{display:inline-flex;align-items:center;justify-content:center;border-radius:16px;font-family:'Oswald',sans-serif;font-weight:500;font-size:13px;text-transform:uppercase}
.btn-dark{background:var(--brown);color:var(--orange)}
.btn-outline{border:2px solid var(--orange);color:var(--brown);background:rgba(255,255,255,.5)}
.pill{display:flex;align-items:center;gap:10px;background:var(--brown);color:var(--orange);border-radius:14px;font-size:9px;font-weight:700;letter-spacing:1.5px;padding:0 14px 0 6px;height:27px}
.pill i{width:19px;height:19px;border-radius:50%;border:2px solid var(--orange)}
.welcome-text p{font-size:11.5px;line-height:15.5px;margin-bottom:16px;color:var(--text)}
.feature{width:160px;text-align:center}
.feature .ico{width:36px;height:36px;border-radius:50%;background:var(--orange);border:3px solid #fbd29b;margin:0 auto 12px}
.feature h3{font-size:13px;color:var(--brown);font-weight:700;line-height:16px;text-transform:uppercase}
.feature p{font-size:9.5px;line-height:12px;margin-top:14px}
.sec-head{display:flex;align-items:center;gap:12px}
.sec-head .mark{width:44px;height:44px;border-radius:50%;border:5px solid var(--orange)}
.sec-head h2{font-size:38px;white-space:nowrap}
.lead{font-size:14px;line-height:16px;text-align:justify}
.ticks{list-style:none}
.ticks li{display:flex;align-items:center;gap:16px;font-size:14px;height:24px}
.ticks svg{flex:none}
.field label{display:block;font-size:14px;color:#777;margin-bottom:6px}
.field div{background:#f5f5f5;border:1px solid #aaa}
.footer{top:3437px;left:0;width:1200px;height:231px;background:var(--brown);color:var(--white)}
.footer h4{font-family:'Lato',sans-serif;font-size:14px;color:var(--orange);text-decoration:underline;font-weight:700}
.footer ul{list-style:none;margin-top:12px}
.footer li{font-size:11px;line-height:19px;display:flex;gap:8px;align-items:flex-start}
.footer li b{color:var(--orange);font-weight:400}
.copy{top:3668px;left:0;width:1200px;height:54px;background:var(--orange);color:var(--brown);font-size:12px}
</style>
</head>
<body>
<div class="abs topline"></div>

<header>
  <div class="abs brand" style="left:105px;top:38px"><span class="brand-dot"></span><span class="brand-name">Golden Sheaf</span></div>
  <div class="abs call">Call Us<div class="num"><svg width="11" height="11" viewBox="0 0 24 24"><path fill="#3d2314" d="M6.6 10.8a15 15 0 006.6 6.6l2.2-2.2c.3-.3.7-.4 1-.2 1.1.4 2.3.6 3.6.6.6 0 1 .4 1 1V20c0 .6-.4 1-1 1A17 17 0 013 4c0-.6.4-1 1-1h3.5c.6 0 1 .4 1 1 0 1.3.2 2.5.6 3.6.1.3 0 .7-.2 1z"/></svg>+1 555 014 2277</div></div>
  <div class="abs follow">Follow Us<div class="socials"><span></span><span></span><span></span><span></span></div></div>
</header>

<nav class="abs nav">
  <a style="left:106px;font-weight:700">Home</a>
  <span class="sep" style="left:202px"></span>
  <a style="left:257px">About</a>
  <span class="sep" style="left:365px"></span>
  <a style="left:425px">Feed</a>
  <span class="sep" style="left:512px"></span>
  <a style="left:574px">Bedding</a>
  <span class="sep" style="left:689px"></span>
  <a style="left:752px">Contact Us</a>
  <a class="quote">Request Quote</a>
</nav>

<section class="abs hero" role="img" aria-label="Aerial photo of the farm buildings and paddocks">
  <h1 class="head-font">THE BEST BEDDING &amp; FEED FOR<br>YOUR HORSE LIVESTOCK OR HOUSEHOLD PET</h1>
  <span class="abs btn btn-dark" style="left:492px;top:171px;width:110px;height:32px">Contact Us</span>
  <span class="abs btn btn-outline" style="left:629px;top:171px;width:111px;height:32px">Request Quote</span>
</section>

<section class="welcome">
  <div class="abs" style="left:117px;top:785px">
    <div class="brand"><span class="brand-dot" style="width:50px;height:50px"></span>
      <div><div class="head-font" style="font-size:14px">WELCOME TO</div><div class="brand-name" style="font-size:36px;line-height:40px">Golden Sheaf</div></div>
    </div>
  </div>
  <div class="abs welcome-text" style="left:117px;top:884px;width:465px">
    <p>Looking for the best bedding and feed for your horse, livestock or household pet look no further.  We use premium locally sourced straw and hay in all of our products and are committed in providing quality products and service.</p>
    <p>Your animal deserves the very best in health and comfort to keep them healthy, strong and happy.  Our products are designed for horses, livestock (goats, cattle and sheep), small caged animals (rabbits, guinea pigs and more).</p>
    <p>Golden Sheaf offers supply and delivery of fresh bedding as well as removal of waste bedding.  Let us deliver you a container of fresh straw and haul your waste bedding away.  A full service solution that is sustainable and responsible.</p>
  </div>
  <div class="abs feature" style="left:90px;top:1080px"><div class="ico"></div><h3>Quality<br>Guaranteed</h3><p>Grown for quality -<br>100% natural with no<br>chemicals or additives</p></div>
  <div class="abs feature" style="left:262px;top:1080px"><div class="ico"></div><h3>Full Service<br>Solution</h3><p>Dedicated in providing<br>a full service solution of bedding<br>supply &amp; waste removal</p></div>
  <div class="abs feature" style="left:432px;top:1080px"><div class="ico"></div><h3>Convenient &amp;<br>Cost Effective</h3><p>Compressed bags, pellets or<br>bulk products saving<br>in shipping costs</p></div>
  <div class="abs" role="img" aria-label="Illustration of a horse framed by an orange horseshoe" style="left:640px;top:800px;width:410px;height:425px;background:linear-gradient(160deg,#f9b35e 0%,#f7941d 100%)"></div>
</section>

<section class="abs" style="top:1312px;left:0;width:1200px;height:660px;background:var(--cream)">
  <div class="abs" role="img" aria-label="Photo of a mare and foal resting on straw bedding" style="left:113px;top:111px;width:517px;height:434px;border:1px solid var(--brown);background:linear-gradient(160deg,#c98b3a 0%,#e3b25a 100%)"></div>
  <div class="abs sec-head" style="left:692px;top:118px"><span class="mark"></span><h2 class="head-font">BEDDING</h2></div>
  <p class="abs lead" style="left:696px;top:211px;width:388px">Hay cubes and pellets are made from premium hay offering a variety of animals a feed that is non-GMO and packed with natural nutrients.  These pellets and cubes are less bulky to handle, store and ship.As well, they reduce the amount of wasted feed.</p>
  <ul class="abs ticks" style="left:700px;top:309px">
    <li><svg width="12" height="12" viewBox="0 0 12 12"><circle cx="6" cy="6" r="6" fill="#3d2314"/><path d="M3 6l2 2 4-4" stroke="#fff" stroke-width="1.6" fill="none"/></svg>100% Natural Chopped Straw</li>
    <li><svg width="12" height="12" viewBox="0 0 12 12"><circle cx="6" cy="6" r="6" fill="#3d2314"/><path d="M3 6l2 2 4-4" stroke="#fff" stroke-width="1.6" fill="none"/></svg>Low Dust</li>
    <li><svg width="12" height="12" viewBox="0 0 12 12"><circle cx="6" cy="6" r="6" fill="#3d2314"/><path d="M3 6l2 2 4-4" stroke="#fff" stroke-width="1.6" fill="none"/></svg>Chemical &amp; Additive Free</li>
    <li><svg width="12" height="12" viewBox="0 0 12 12"><circle cx="6" cy="6" r="6" fill="#3d2314"/><path d="M3 6l2 2 4-4" stroke="#fff" stroke-width="1.6" fill="none"/></svg>Clean &amp; Highly Absorbent</li>
    <li><svg width="12" height="12" viewBox="0 0 12 12"><circle cx="6" cy="6" r="6" fill="#3d2314"/><path d="M3 6l2 2 4-4" stroke="#fff" stroke-width="1.6" fill="none"/></svg>Cheaper than Wood Shavings</li>
    <li><svg width="12" height="12" viewBox="0 0 12 12"><circle cx="6" cy="6" r="6" fill="#3d2314"/><path d="M3 6l2 2 4-4" stroke="#fff" stroke-width="1.6" fill="none"/></svg>Economic – less used &amp; less wasted</li>
    <li><svg width="12" height="12" viewBox="0 0 12 12"><circle cx="6" cy="6" r="6" fill="#3d2314"/><path d="M3 6l2 2 4-4" stroke="#fff" stroke-width="1.6" fill="none"/></svg>Environmentally Friendly – Recyclable &amp; Compostable</li>
  </ul>
  <span class="abs pill" style="left:700px;top:511px"><i></i>READ MORE</span>
</section>

<section class="abs" style="top:1972px;left:0;width:1200px;height:639px">
  <div class="abs sec-head" style="left:112px;top:92px"><span class="mark"></span><h2 class="head-font">FEEDING</h2></div>
  <p class="abs lead" style="left:116px;top:189px;width:386px">Hay cubes and pellets are made from premium hay offering a variety of animals a feed that is non-GMO and packed with natural nutrients.  These pellets and cubes are less bulky to handle, store and ship.As well, they reduce the amount of wasted feed.</p>
  <ul class="abs ticks" style="left:112px;top:289px">
    <li><svg width="12" height="12" viewBox="0 0 12 12"><circle cx="6" cy="6" r="6" fill="#3d2314"/><path d="M3 6l2 2 4-4" stroke="#fff" stroke-width="1.6" fill="none"/></svg>100% Natural</li>
    <li><svg width="12" height="12" viewBox="0 0 12 12"><circle cx="6" cy="6" r="6" fill="#3d2314"/><path d="M3 6l2 2 4-4" stroke="#fff" stroke-width="1.6" fill="none"/></svg>Chemical &amp; Additive Free</li>
    <li><svg width="12" height="12" viewBox="0 0 12 12"><circle cx="6" cy="6" r="6" fill="#3d2314"/><path d="M3 6l2 2 4-4" stroke="#fff" stroke-width="1.6" fill="none"/></svg>Available in Pellets or Cubes</li>
    <li><svg width="12" height="12" viewBox="0 0 12 12"><circle cx="6" cy="6" r="6" fill="#3d2314"/><path d="M3 6l2 2 4-4" stroke="#fff" stroke-width="1.6" fill="none"/></svg>High Protein Content</li>
    <li><svg width="12" height="12" viewBox="0 0 12 12"><circle cx="6" cy="6" r="6" fill="#3d2314"/><path d="M3 6l2 2 4-4" stroke="#fff" stroke-width="1.6" fill="none"/></svg>Eliminate Waste In Feeding</li>
    <li><svg width="12" height="12" viewBox="0 0 12 12"><circle cx="6" cy="6" r="6" fill="#3d2314"/><path d="M3 6l2 2 4-4" stroke="#fff" stroke-width="1.6" fill="none"/></svg>Clean - Eliminates Dust From Feeding Baled Hay</li>
    <li><svg width="12" height="12" viewBox="0 0 12 12"><circle cx="6" cy="6" r="6" fill="#3d2314"/><path d="M3 6l2 2 4-4" stroke="#fff" stroke-width="1.6" fill="none"/></svg>Cost Effective</li>
  </ul>
  <span class="abs pill" style="left:112px;top:496px"><i></i>READ MORE</span>
  <div class="abs" role="img" aria-label="Close-up photo of a horse eating dry hay" style="left:608px;top:86px;width:513px;height:470px;border:1px solid var(--brown);background:linear-gradient(135deg,#6b5f55 0%,#b8925a 100%)"></div>
</section>

<section class="abs" style="top:2611px;left:0;width:1200px;height:621px;background:var(--grey)">
  <div class="abs sec-head" style="left:452px;top:48px"><span class="mark"></span><h2 class="head-font">REQUEST A QUOTE</h2></div>
  <p class="abs" style="left:170px;top:133px;width:860px;text-align:center;font-size:13.5px;line-height:17px;color:#666">Sit amet, cu per porro dolore nostro, partem integre corpora per ea, tation ornatus mel ad. Brute voluptatibus an est, torquatos, nesciunt. partem integre corpora per ea, tation sit amet, cu per porro dolore nostrotorquatos, nesciunt. per cu utroque partem integre corpora per ea, tation sit amet, cu per porro dolore nostro</p>
  <div class="abs field" style="left:255px;top:224px;width:325px"><label>Name</label><div style="height:37px"></div></div>
  <div class="abs field" style="left:598px;top:224px;width:324px"><label>Email</label><div style="height:37px"></div></div>
  <div class="abs field" style="left:255px;top:302px;width:667px"><label>Subject</label><div style="height:37px"></div></div>
  <div class="abs field" style="left:255px;top:384px;width:667px"><label>Message</label><div style="height:110px"></div></div>
  <span class="abs pill" style="left:531px;top:552px"><i></i>READ MORE</span>
</section>

<section class="abs" style="top:3232px;left:0;width:1200px;height:205px">
  <div class="abs" role="img" aria-label="Photo of horses grazing in a pasture" style="left:0;top:0;width:1200px;height:205px;background:linear-gradient(180deg,var(--sky-soft) 0%,var(--field-soft) 100%)"></div>
  <h2 class="abs head-font" style="left:342px;top:58px;font-size:32px;line-height:40px;white-space:nowrap">SUBSCRIBE TO NEWSLETTER</h2>
  <div class="abs" style="left:313px;top:108px;width:715px;height:50px;background:#fff;border:1px solid #ccc;font-size:13px;color:#333;padding:17px 40px">Enter Your Email</div>
  <div class="abs" style="left:1028px;top:108px;width:130px;height:50px;background:var(--brown);color:#fff;font-size:14px;font-weight:700;display:flex;align-items:center;justify-content:center">SUBSCRIBE</div>
</section>

<footer class="abs footer">
  <div class="abs" style="left:125px;top:45px;width:240px;text-align:center">
    <span class="brand-dot" style="display:block;width:56px;height:56px;margin:0 auto 14px"></span>
    <div class="brand-name" style="color:#fff;font-size:34px">Golden Sheaf</div>
  </div>
  <div class="abs" style="left:451px;top:45px"><h4>QUICK LINKS</h4>
    <ul><li><b>▶</b>Home</li><li><b>▶</b>About</li><li><b>▶</b>Feed</li><li><b>▶</b>Bedding</li><li><b>▶</b>Contact Us</li></ul></div>
  <div class="abs" style="left:655px;top:47px"><h4>CONTACT US</h4>
    <ul><li><b>●</b>412 Meadowbrook Road<br>Fairbanks, Alaska 99701</li><li><b>✆</b>555-014-2277</li><li><b>✉</b>hello@goldensheaf.example</li><li><b>◎</b>goldensheaf.example</li></ul></div>
  <div class="abs" style="left:918px;top:45px"><h4>NEWSLETTER</h4>
    <div style="display:flex;margin-top:12px"><div style="width:137px;height:26px;background:#fff;font-size:9px;color:#999;padding:8px 12px">Email Address</div><div style="width:26px;height:26px;background:var(--orange);display:flex;align-items:center;justify-content:center"><svg width="9" height="10"><path d="M0 0l9 5-9 5z" fill="#3d2314"/></svg></div></div>
    <h4 style="margin-top:10px">FOLLOW US</h4>
    <div class="socials" style="margin-top:8px"><span style="width:18px;height:18px;background:#fff"></span><span style="width:18px;height:18px;background:#fff"></span><span style="width:18px;height:18px;background:#fff"></span><span style="width:18px;height:18px;background:#fff"></span><span style="width:18px;height:18px;background:#fff"></span></div>
  </div>
</footer>

<div class="abs copy">
  <span class="abs" style="left:125px;top:20px">Copyright © 2021, Northfield Studio, All Right Reserved</span>
  <span class="abs" style="left:933px;top:20px">Delivery in Canada &amp; USA</span>
</div>
</body>
</html>
```